Business Cards Design for the electrical wholesaler: clean bold dynamic :)

We need a business card design that would follow our latest brand guidelines. As an electrical wholesaler we want to bring a fresh look and feel into the industry. The design should be clean bold and dynamic. It should come alive with the renewed energy of our green colour. Our grey colour should keep things balanced and complement the notion of maturity and responsibility. We employ Lato as a corporate font however are not bound by this font and we’re open to interpretation here.

Target Market(s)

Electrical contractors

Industry/Entity Type

Business

Contact Information for Business Card

Logo
Name & Surname: Halyna Dorosh
Job Title: Director of Marketing
Email: halya.dorosh@quillmail.example
Cell phone: XXX.XXX.XXXX
Address: 20517 - 87 Ave. Edmonton, AB, Canada. T6K 4N8
Business Phone: 780.555.0184
Website: www.brovix.example

Font styles to use
Other font styles liked:
• Lato

Requirements
Must have
• Logo & website
Nice to have
• Brand elements - some of them you may find in the attached Brand Guidelines (e.g. three lines on the background signifying "W")

```html
<!DOCTYPE html>
<html lang="en">
<head>
<meta charset="utf-8">
<title>Brovix Business Card</title>
<link rel="stylesheet" href="https://fonts.googleapis.com/css2?family=Roboto:wght@400;500&family=Exo+2:wght@500&display=swap">
<style>
  :root {
    --stage: #c9c9c9;
    --green-light: #80bd26;
    --green-dark: #5ea92f;
    --green-text: #78b72a;
    --grey-ink: #4a4d52;
    --grey-soft: #55585c;
    --paper: #f2f2f2;
    --paper-edge: #e4e4e4;
  }
  * { box-sizing: border-box; margin: 0; padding: 0; }
  html, body { width: 1200px; height: 576px; overflow: hidden; }
  body {
    background: var(--stage);
    font-family: "Roboto", Arial, sans-serif;
    position: relative;
  }
  .card {
    position: absolute;
    top: 138px;
    height: 294px;
    border-radius: 12px;
    overflow: hidden;
  }
  .card--front {
    left: 82px;
    width: 484px;
    background: linear-gradient(160deg, var(--green-light), var(--green-dark));
    display: flex;
    align-items: center;
    justify-content: center;
  }
  .card--back {
    left: 602px;
    width: 480px;
    background: linear-gradient(180deg, var(--paper), var(--paper-edge));
  }
  .brand {
    display: flex;
    align-items: center;
    gap: 10px;
    font-family: "Roboto", Arial, sans-serif;
    font-weight: 500;
    color: var(--grey-ink);
    letter-spacing: 0.5px;
    white-space: nowrap;
  }
  .brand__dot {
    width: 26px;
    height: 26px;
    border-radius: 50%;
    background: var(--grey-ink);
  }
  .card--front .brand { font-size: 50px; }
  .card--back .brand {
    position: absolute;
    left: 50px;
    top: 118px;
    font-size: 40px;
  }
  .card--back .brand__dot {
    width: 22px;
    height: 22px;
    background: var(--green-text);
  }
  .contact {
    position: absolute;
    left: 256px;
    top: 80px;
    width: 210px;
    color: var(--grey-soft);
  }
  .contact__name {
    font-family: "Exo 2", Arial, sans-serif;
    font-weight: 500;
    font-size: 20px;
    line-height: 24px;
    color: var(--green-text);
  }
  .contact__title { font-size: 12.5px; line-height: 18px; }
  .contact__address { margin-top: 14px; font-size: 12.5px; line-height: 16px; }
  .contact__list { list-style: none; margin-top: 8px; font-size: 12px; }
  .contact__item {
    display: flex;
    align-items: center;
    gap: 6px;
    line-height: 17px;
    white-space: nowrap;
  }
  .icon { width: 11px; height: 11px; flex: none; }
</style>
</head>
<body>
  <section class="card card--front" aria-label="Card front">
    <div class="brand"><span class="brand__dot"></span>Brovix</div>
  </section>

  <section class="card card--back" aria-label="Card back">
    <div class="brand"><span class="brand__dot"></span>Brovix</div>
    <div class="contact">
      <p class="contact__name">Halyna Dorosh</p>
      <p class="contact__title">Director of Marketing</p>
      <p class="contact__address">20517 - 87 Ave. Edmonton,<br>AB, Canada. T6K 4N8</p>
      <ul class="contact__list">
        <li class="contact__item">
          <svg class="icon" viewBox="0 0 12 12" aria-hidden="true"><circle cx="6" cy="6" r="6" fill="#78b72a"/><path d="M3.6 3.4c.4-.4.9-.3 1.1.1l.4.8c.1.3 0 .5-.2.7l-.3.3c.4.8 1 1.4 1.8 1.8l.3-.3c.2-.2.4-.3.7-.2l.8.4c.4.2.5.7.1 1.1-.5.5-1.2.6-1.9.3C5 8 4 7 3.4 5.6c-.3-.7-.2-1.5.2-2.2z" fill="#fff"/></svg>
          780.555.0184
        </li>
        <li class="contact__item">
          <svg class="icon" viewBox="0 0 12 12" aria-hidden="true"><circle cx="6" cy="6" r="6" fill="#78b72a"/><rect x="3" y="4" width="6" height="4.2" fill="none" stroke="#fff" stroke-width=".9"/><path d="M3 4l3 2.3L9 4" fill="none" stroke="#fff" stroke-width=".9"/></svg>
          halya.dorosh@quillmail.example
        </li>
        <li class="contact__item">
          <svg class="icon" viewBox="0 0 12 12" aria-hidden="true"><circle cx="6" cy="6" r="6" fill="#78b72a"/><circle cx="6" cy="6" r="3" fill="none" stroke="#fff" stroke-width=".8"/><path d="M3 6h6M6 3c-1.3 1.6-1.3 4.4 0 6M6 3c1.3 1.6 1.3 4.4 0 6" fill="none" stroke="#fff" stroke-width=".7"/></svg>
          www.brovix.example
        </li>
      </ul>
    </div>
  </section>
</body>
</html>
```